Redesign This Psychology Website

We would like a slight redesign of this successful psychology (relationship counselling) website:

www.TheKelvaleClinic.com.au

We are updating the website, and we'd like a slight refresh of the design and style.

Please keep to very similar colours, and use the same logo. We're looking for around 10 page templates, however the main one is the home page.

Keep in mind, this website already converts quite well, so we want a new, fresh design in keeping with this one. Please don't bother designing something too extremely different.

thanks :)

Target Market(s)

couples who are looking for relationship counselling. Men and women, 25 - 70, across Australia

Industry/Entity Type

Psychology

Number of Pages Required

5+ page

Font styles to use
Sans Serif

Colors
87cfc6
b7a5cd
ec1f27
ffffff
cee9f5

Requirements
Must have
• a similar look to the current design, just looking for a slight refresh.
• Search bar
• Areas for lots of photos
• same logo
• lots of content areas
Nice to have
• great content areas, where we can display a lot of content and our areas.
Should not have
• no colors like orange, etc.
• should not have a totally different feel.

```html
<!DOCTYPE html>
<html lang="en">
<head>
<meta charset="utf-8">
<title>The Kelvale Clinic – Relationship Counselling</title>
<link rel="stylesheet" href="https://fonts.googleapis.com/css2?family=Didact+Gothic&family=Questrial&display=swap">
<style>
:root{
  --teal-dark:#14808a;
  --teal:#1e939c;
  --teal-soft:#87cfc6;
  --sky:#cee9f5;
  --lilac:#b7a5cd;
  --red:#ec1f27;
  --card-orange:#ef7b45;
  --card-rust:#c8672e;
  --card-teal:#4fb8c1;
  --grey-bg:#f1f1f1;
  --ink:#4d4d4d;
  --ink-soft:#777;
  --line:#dcdcdc;
  --white:#ffffff;
}
*{box-sizing:border-box;margin:0;padding:0}
html,body{width:1200px;height:4433px;overflow:hidden;background:var(--white)}
body{position:relative;font-family:"Didact Gothic",sans-serif;color:var(--ink);font-size:11px;line-height:1.55}
a{color:var(--teal);text-decoration:underline}
.abs{position:absolute}

/* top bar */
.topbar{top:0;left:0;width:1200px;height:30px;background:var(--teal-dark);color:var(--white);font-size:11px}
.topbar ul{list-style:none;display:flex;gap:14px;position:absolute;top:8px}
.topbar .left{left:162px}.topbar .right{right:160px}

/* header */
.header{top:30px;left:0;width:1200px;height:103px}
.brand{position:absolute;left:162px;top:20px;display:flex;align-items:center;gap:10px}
.brand-dot{width:46px;height:46px;border-radius:50%;background:var(--teal)}
.brand-name{font-family:"Questrial",sans-serif;font-size:27px;color:var(--teal);line-height:1}
.brand-sub{font-family:"Questrial",sans-serif;font-size:12px;color:var(--teal);margin-top:5px}
.callus{position:absolute;left:585px;top:14px;font-size:15px;color:var(--ink)}
.callus b{color:var(--teal);font-weight:400;font-size:17px}
.callus svg{vertical-align:-3px;margin:0 4px}
.social{position:absolute;left:765px;top:14px;display:flex;gap:6px}
.social span{width:22px;height:22px;border-radius:50%;background:var(--teal)}
.social span:nth-child(2){background:var(--red)}
.cart{position:absolute;left:900px;top:12px;width:140px;height:28px;background:var(--red);color:var(--white);border-radius:3px;text-align:center;line-height:28px;font-size:12px}
.search{position:absolute;left:760px;top:56px;width:280px;height:28px;border:1px solid var(--line);border-radius:3px;padding:0 10px;line-height:26px;color:var(--ink-soft);font-size:11px}
.search svg{position:absolute;right:8px;top:7px}

/* nav */
.nav{top:133px;left:0;width:1200px;height:44px;background:var(--teal)}
.nav ul{list-style:none;display:flex;position:absolute;left:162px;top:0;height:44px}
.nav li{color:var(--white);font-size:12px;padding:0 20px;line-height:44px}
.nav li.active{background:var(--teal-soft);padding:0 32px}

/* hero */
.hero{top:177px;left:0;width:1200px;height:385px;background:linear-gradient(180deg,#e9eef0 0%,#c9dbb4 45%,#8fb35e 75%,#6f9a3f 100%)}
.hero-video{position:absolute;left:162px;top:59px;width:444px;height:311px;background:linear-gradient(135deg,#d9c3a5,#8f7a62);border:6px solid var(--white);box-shadow:0 2px 10px rgba(0,0,0,.25)}
.play{position:absolute;left:50%;top:50%;width:56px;height:56px;margin:-28px 0 0 -28px;border-radius:50%;border:3px solid var(--white);background:rgba(0,0,0,.25)}
.play:after{content:"";position:absolute;left:21px;top:15px;border-left:18px solid var(--white);border-top:11px solid transparent;border-bottom:11px solid transparent}

/* service cards */
.services{top:562px;left:0;width:1200px;height:473px;background:var(--grey-bg)}
.svc{position:absolute;top:44px;width:199px;height:369px;background:var(--white);box-shadow:0 1px 4px rgba(0,0,0,.12);text-align:center}
.svc-head{height:44px;color:var(--white);font-size:12.5px;line-height:1.25;display:flex;align-items:center;justify-content:center;padding:0 10px}
.svc-photo{height:140px;margin:8px}
.svc p{font-size:10.5px;color:var(--ink-soft);padding:0 14px;line-height:1.5}
.svc .svc-link{display:block;margin-top:6px;font-size:10.5px;color:var(--ink)}
.svc .btn{position:absolute;left:50%;bottom:16px;transform:translateX(-50%);width:84px;height:24px;border-radius:12px;color:var(--white);font-size:10.5px;line-height:24px}
.o{background:var(--card-orange)}.t{background:var(--card-teal)}.r{background:var(--card-rust)}

/* main column */
.main{top:1070px;left:162px;width:578px;height:2600px;overflow:hidden;font-size:12px;line-height:1.65}
.main h2{font-family:"Questrial",sans-serif;font-weight:400;font-size:18px;color:var(--ink);margin:0 0 12px}
.main p{margin:0 0 11px}
.main .hi{color:var(--teal)}
.main b{color:var(--teal);font-weight:400}
.block{margin-bottom:30px}
.ticks{list-style:none;columns:2;column-gap:40px;margin:6px 0 12px}
.ticks li{position:relative;padding-left:18px;margin-bottom:6px;break-inside:avoid}
.ticks li:before{content:"";position:absolute;left:2px;top:3px;width:5px;height:9px;border:solid var(--teal);border-width:0 2px 2px 0;transform:rotate(40deg)}
.bullets,.locs{list-style:none;columns:2;column-gap:40px;margin:6px 0 12px}
.bullets li,.locs li{position:relative;padding-left:14px;margin-bottom:6px}
.bullets li:before,.locs li:before{content:"";position:absolute;left:2px;top:7px;width:5px;height:5px;border-radius:50%;background:var(--teal)}
.photo{width:578px;margin:26px 0 30px;box-shadow:0 1px 4px rgba(0,0,0,.15)}
.photo.one{height:180px;background:linear-gradient(90deg,#f3ede4,#e2cdb2 50%,#c79e75)}
.photo.two{height:210px;background:linear-gradient(90deg,#ede6dc,#d6c1a6 55%,#a88a6c)}
.profile{background:var(--grey-bg);display:flex;gap:18px;padding:12px;margin-top:18px}
.profile-photo{width:130px;height:120px;background:linear-gradient(135deg,#c9a88c,#8a6a57);flex:none}
.profile h3{font-family:"Questrial",sans-serif;font-weight:400;font-size:17px;color:var(--teal)}
.profile .role{color:var(--ink-soft);margin-bottom:4px}

/* sidebar */
.side{top:1070px;left:762px;width:278px}
.finder{position:absolute;top:0;width:278px;height:245px;background:var(--teal);padding:14px 16px;text-align:center;color:var(--white)}
.finder h4{font-family:"Questrial",sans-serif;font-weight:400;font-size:13px;line-height:1.3;margin-bottom:12px}
.finder .field{height:26px;background:var(--white);border-radius:2px;margin-bottom:9px;color:var(--ink-soft);text-align:left;padding:0 8px;line-height:26px;font-size:10.5px}
.finder .go{width:90px;height:26px;margin:10px auto 0;background:var(--red);border-radius:2px;line-height:26px;font-size:11px}
.ad{position:absolute;width:278px;color:var(--white);box-shadow:0 1px 4px rgba(0,0,0,.15)}
.ad .txt{position:absolute;left:16px;top:30px;width:150px;font-family:"Questrial",sans-serif;font-size:15px;line-height:1.25}
.ad .cta{position:absolute;right:0;bottom:12px;width:110px;height:24px;background:var(--red);font-size:11px;line-height:24px;padding-left:14px}
.ad.mood{height:195px;background:linear-gradient(90deg,#2e5e8f,#6f93b5 60%,#a6bacd)}
.ad.gp{height:186px;background:linear-gradient(90deg,#b9c9cf,#e5e9ea 55%,#f4f4f4)}
.ad.gp .txt{left:120px;top:50px;color:var(--ink)}
.vid-head{position:absolute;width:278px;height:32px;background:var(--teal);color:var(--white);text-align:center;line-height:32px;font-size:12px}
.vid{position:absolute;width:278px;height:198px;background:linear-gradient(135deg,#dbc6b0,#9b8874)}
.tile{position:absolute;width:278px;height:162px;box-shadow:0 1px 4px rgba(0,0,0,.15)}
.tile .label{position:absolute;left:0;bottom:0;width:100%;height:30px;background:var(--teal);color:var(--white);font-size:12px;line-height:30px;padding-left:12px}
.tile.assess{background:linear-gradient(135deg,#e8d3bd,#b99274)}
.tile.about{background:linear-gradient(135deg,#d3dfe8,#8fa7b9)}
.mini{position:absolute;width:278px;height:118px;display:flex;background:var(--white);box-shadow:0 1px 4px rgba(0,0,0,.12)}
.mini .pic{width:130px;height:118px;flex:none}
.mini .copy{padding:20px 12px 0;font-family:"Questrial",sans-serif;font-size:13.5px;line-height:1.3;color:var(--ink)}
.mini .copy a{color:var(--teal)}
.mini .cta{position:absolute;right:0;bottom:10px;width:110px;height:22px;background:var(--red);color:var(--white);font-size:11px;line-height:22px;padding-left:14px}

/* blog */
.blog{top:3680px;left:0;width:1200px;height:330px}
.blog h2{position:absolute;left:162px;top:0;font-family:"Questrial",sans-serif;font-weight:400;font-size:16px}
.post{position:absolute;top:40px;width:218px;height:190px;background:var(--white);box-shadow:0 1px 5px rgba(0,0,0,.15)}
.post .pic{height:110px}
.post .date{background:var(--red);color:var(--white);font-size:10px;padding:2px 8px;display:inline-block;margin:8px 0 0 8px}
.post h5{font-weight:400;font-size:11px;color:var(--ink);padding:6px 8px 0}
.post .more{font-size:10px;color:var(--teal);padding:4px 8px}
.arrow{position:absolute;top:120px;width:28px;height:28px;border-radius:50%;background:var(--red)}
.arrow svg{position:absolute;left:9px;top:8px}
.readmore{position:absolute;left:0;top:278px;width:1200px;text-align:center;font-family:"Questrial",sans-serif;font-size:15px}
.readmore .btn{display:block;width:100px;height:26px;margin:10px auto 0;background:var(--red);color:var(--white);border-radius:3px;font-size:11px;line-height:26px}

/* footer */
.footer{top:4094px;left:0;width:1200px;height:339px;background:var(--teal);color:var(--white);text-align:center}
.login{position:absolute;left:162px;top:70px;width:878px;height:62px;display:flex;align-items:center;gap:18px;padding-left:46px}
.login h4{font-family:"Questrial",sans-serif;font-weight:400;font-size:19px;margin-right:14px}
.login .in{width:250px;height:26px;background:var(--white);border-radius:3px;color:var(--ink-soft);font-size:10.5px;text-align:left;padding:0 10px;line-height:26px}
.login .send{width:82px;height:26px;background:var(--teal-dark);border:1px solid rgba(255,255,255,.5);border-radius:3px;font-size:11px;line-height:24px}
.foot-call{position:absolute;left:0;top:212px;width:1200px;font-size:15px}
.foot-links{position:absolute;left:0;top:255px;width:1200px;font-size:11px}
.foot-links span{margin:0 10px;text-decoration:underline}
.foot-social{position:absolute;left:0;top:282px;width:1200px;display:flex;justify-content:center;gap:6px}
.foot-social span{width:18px;height:18px;border-radius:50%;background:var(--white);opacity:.9}
.copy-note{position:absolute;left:0;top:312px;width:1200px;font-size:10px}
</style>
</head>
<body>

<div class="abs topbar">
  <ul class="left"><li>Home</li><li>|</li><li>About</li><li>|</li><li>Resources</li><li>|</li><li>Blog</li><li>|</li><li>Shop</li></ul>
  <ul class="right"><li>Join Our Associate Program</li><li>|</li><li>Marriage Counselling</li><li>|</li><li>Relationship Counselling</li></ul>
</div>

<header class="abs header">
  <div class="brand">
    <span class="brand-dot"></span>
    <div><div class="brand-name">The Kelvale Clinic</div><div class="brand-sub">couples counselling across Australia</div></div>
  </div>
  <div class="callus">Call Us<svg width="16" height="16" viewBox="0 0 24 24"><path fill="#1e939c" d="M6.6 10.8a15 15 0 0 0 6.6 6.6l2.2-2.2c.3-.3.7-.4 1-.2 1.1.4 2.3.6 3.6.6.6 0 1 .4 1 1V20c0 .6-.4 1-1 1A17 17 0 0 1 3 4c0-.6.4-1 1-1h3.5c.6 0 1 .4 1 1 0 1.3.2 2.5.6 3.6.1.3 0 .7-.2 1z"/></svg><b>1300 555 017</b></div>
  <div class="social"><span></span><span></span><span></span></div>
  <div class="cart">My Cart $ (0.00)</div>
  <div class="search">Relationship Information Topic
    <svg width="13" height="13" viewBox="0 0 24 24"><circle cx="10" cy="10" r="7" fill="none" stroke="#777" stroke-width="2.5"/><path d="M15 15l6 6" stroke="#777" stroke-width="2.5"/></svg>
  </div>
</header>

<nav class="abs nav">
  <ul>
    <li class="active">Counselling Types</li>
    <li>Relationship Counselling Locations</li>
    <li>Sex Therapy Locations</li>
    <li>Quizzes</li>
    <li>F.A.Q'S</li>
    <li>Contact</li>
  </ul>
</nav>

<section class="abs hero" role="img" aria-label="Photo of a smiling couple in a green field of flowers">
  <div class="hero-video" role="img" aria-label="Video still of a counsellor speaking"><span class="play"></span></div>
</section>

<section class="abs services">
  <div class="svc" style="left:162px">
    <div class="svc-head o">Relationship Counselling</div>
    <div class="svc-photo" role="img" aria-label="Photo of a couple talking" style="background:linear-gradient(135deg,#e6d2bd,#a98467)"></div>
    <p>Communication, Recovering from an affair, Loss of intimacy &amp; love, Power battles…<a class="svc-link">Take our Relationship Quiz</a></p>
    <div class="btn o">Read More</div>
  </div>
  <div class="svc" style="left:408px">
    <div class="svc-head t">Sex Therapy Counselling</div>
    <div class="svc-photo" role="img" aria-label="Photo of a couple in bed" style="background:linear-gradient(135deg,#eee7df,#bfa58d)"></div>
    <p>Low libido, Erectile difficulties, Premature ejaculation, Differing libidos, Porn addiction…<a class="svc-link">Take our Sex Quiz</a></p>
    <div class="btn t">Read More</div>
  </div>
  <div class="svc" style="left:650px">
    <div class="svc-head r">Anger Management Counselling</div>
    <div class="svc-photo" role="img" aria-label="Photo of an angry man" style="background:linear-gradient(135deg,#d9d4cf,#7f7369)"></div>
    <p>Managing angry outbursts, expressing your anger in healthy ways…<a class="svc-link">Take our Anger Test</a></p>
    <div class="btn r">Read More</div>
  </div>
  <div class="svc" style="left:896px">
    <div class="svc-head t">Narcissism Counselling</div>
    <div class="svc-photo" role="img" aria-label="Photo of a woman looking worried" style="background:linear-gradient(135deg,#e2d3c6,#96786a)"></div>
    <p>Managing narcissistic, superior, entitled, arrogant and lack of empathy…<a class="svc-link">Check your Narcissism Profile</a></p>
    <div class="btn t">Read More</div>
  </div>
</section>

<main class="abs main">
  <div class="block">
    <h2>We Specialise in Relationship &amp; Marriage Counselling</h2>
    <p>At The Kelvale Clinic, we are a group of PSYCHOLOGISTS, Australia wide who are <b>passionate about relationships and helping you with yours.</b></p>
    <p>Our vision is to provide the most highly regarded and comprehensive <span class="hi">marriage counselling</span> and <span class="hi">relationship counselling</span>, and <span class="hi">sex therapy</span> in Australia, at reasonable and affordable rates.</p>
    <p>When we are experiencing relationship and marriage problems, there can be a lot of pain and confusion, and it can often be difficult to cope with the other areas of our lives when we are struggling with problems with our partner.</p>
    <p>We are not taught about relationships and how to have a good one in our schools, so most of us are doing the best we know how, but lack the knowledge on how to create a better relationship.</p>
  </div>
  <div class="block">
    <h2>Our Kelvale Relationship Psychologists</h2>
    <p>Our team of 75 hand chosen <b>Registered Psychologists</b> in 81 locations Australia wide, are individually selected for their knowledge, experience, compassion, and continued approach to marriage counselling and sexual therapy.</p>
    <p>In addition all our Psychologists take part in our Initial Relationship Counselling Methodologies Training and yearly in-house conferences, ensuring you are in safe and experienced hands.</p>
    <p class="hi">As we are Psychologists, you may be eligible for Medicare &amp; Private Health Insurance Rebates. We are highly experienced and can help you with all kinds of relationship difficulties.</p>
    <p>Here are some of the common ones:</p>
    <ul class="ticks">
      <li>Affairs</li><li>Controlling behaviour</li><li>Verbal abuse</li><li>Imbalance of power</li><li>Lack of intimacy</li><li>Poor communication</li><li>Loss of love</li><li>Relationship neglect</li><li>Sexual problems</li>
      <li>Problems from childhood</li><li>Problems with parenting your children</li><li>Step children and in-laws</li><li>All forms of family problems</li><li>Anger management problems</li><li>Porn addiction problems</li><li>Pre-marriage programs</li><li>Affairs</li>
    </ul>
  </div>
  <div class="block">
    <h2>Our Relationship Counselling Approach</h2>
    <p>It is an important part of our policy to take a <span class="hi">very positive approach</span> to our relationship counselling.</p>
    <p>We feel it is important to really understand the problems and perspectives of each of you, and at the same time, we find that most couples are looking to find a positive action plan and way through their problems to make changes which have a positive impact and a real sense of hope for their relationship.</p>
    <p>Read more about our approach to counselling in our <span class="hi">relationship counselling sessions, and frequently asked questions about the relationship and marriage counselling process.</span></p>
  </div>
  <div class="block">
    <h2>Our Relationship Counselling Locations across Australia</h2>
    <p>Here are some of the common ones:</p>
    <ul class="locs">
      <li><a>Sydney</a> – 19 centres</li><li><a>Canberra</a> – 2 centres</li><li><a>Melbourne</a> – 21 centres</li><li><a>Perth</a> – 13 centres</li><li><a>Brisbane</a> – 14 centres</li><li><a>Wollongong</a> – 1 centre</li><li><a>Central Coast</a> – 2 centres</li>
      <li><a>Adelaide</a> – 4 centres</li><li><a>Gold Coast</a> – 3 centres</li><li><a>Sunshine Coast</a> – 2 centres</li><li><a>Cairns</a> – 1 centre</li><li><a>Townsville</a> – 1 centre</li><li><a>Wodonga</a> – 1 centre</li>
    </ul>
    <p>Certain clinics also provide after hours and Saturday sessions for your convenience. Click the <span class="hi">Locations</span> tab for more information about one of our caring psychologists in your area.</p>
  </div>
  <div class="photo one" role="img" aria-label="Photo of a happy couple smiling together"></div>
  <div class="block">
    <h2>Communication is a vital skill but not often taught to us.</h2>
    <p>Most people find that their ways of communicating with each other are what hamper us from having a happy healthy relationship.</p>
    <p>Effective Interpersonal Communication skills are not something that we are usually taught. But for almost everyone who is having difficulties in their relationship, they feel that they are trying to communicate their thoughts and feelings but that their partner is not listening.</p>
    <p>Most people then find that they themselves don't want to listen when they experience their partner as not wanting to listen to them, so the net effect is that neither person gets listened to, and both are frustrated.</p>
    <p>So learning how to communicate your honest thoughts and feelings in a way that your partner does truly listen is a crucial skill for you to find that you are in a fulfilling relationship. We can show you some simple but effective principles on how to do this with each other.</p>
  </div>
  <div class="photo two" role="img" aria-label="Photo of a couple relaxing close together"></div>
  <div class="block">
    <h2>We as individuals have specific patterns in our relationships</h2>
    <p>We can also assist you if you want individual help and guidance on your relationship, as you can learn what the patterns in your relationships are showing you about yourself.</p>
    <p>If you have been in a number of relationships and have found yourself repeating the same kind of experiences, which is often the way our relationships play out, we can help you discover the patterns that you might be unwittingly setting up, so you can change these and move into more rewarding relationships in the future.</p>
    <p>Want more information? Please feel free to browse our free articles on common relationship problems you may be encountering including:</p>
    <ul class="bullets">
      <li>Why relationships go wrong</li><li>How to be yourself in your relationship</li>
      <li>How to recover from an affair</li><li>The secret to more sex</li>
    </ul>
    <p><b>For the latest short, up to date articles on relationships,</b> relationship problems and relationship counselling, please also check out our relationship counselling blog.</p>
    <div class="profile">
      <div class="profile-photo" role="img" aria-label="Portrait photo of the psychologist"></div>
      <div>
        <h3>Marla</h3>
        <div class="role">Registered Psychologist Brisbane</div>
        <p>B Soc Work; B Ed (Hons) &amp; Soc Sci (Psych), Grad Dip Psych; Grad Dip Couns; M Couns</p>
        <p>You can read more about <span class="hi">relationship counselling</span> here.</p>
      </div>
    </div>
  </div>
</main>

<aside class="abs side">
  <div class="finder">
    <h4>Find Our Psychologist<br>Near You</h4>
    <div class="field">Type of Counselling</div>
    <div class="field">Location</div>
    <div class="field">Postcode</div>
    <div class="go">Search</div>
  </div>
  <div class="ad mood" style="top:266px" role="img" aria-label="Photo of a stressed woman"><div class="txt">Is Anxiety, Depression Or Stress bothering YOU?</div><div class="cta">Click Here ›</div></div>
  <div class="ad gp" style="top:482px" role="img" aria-label="Photo of a doctor at a desk"><div class="txt">Information for referring GPs &amp; Health Professionals</div><div class="cta">Click Here ›</div></div>
  <div class="vid-head" style="top:695px">What To Expect From Counselling</div>
  <div class="vid" style="top:727px" role="img" aria-label="Video still of a counselling session"><span class="play"></span></div>
  <div class="tile assess" style="top:955px" role="img" aria-label="Photo of a couple embracing"><div class="label">Our Kelvale Relationship Assessment</div></div>
  <div class="tile about" style="top:1132px" role="img" aria-label="Photo of a couple walking"><div class="label">Find out more about us</div></div>

  <div class="mini" style="top:1310px"><div class="pic" role="img" aria-label="Photo of an upset couple" style="background:linear-gradient(135deg,#d8c5b4,#8a6e5c)"></div><div class="copy">How to deal with an affair?</div><div class="cta">Click Here ›</div></div>
  <div class="mini" style="top:1443px"><div class="pic" role="img" aria-label="Photo of two men together" style="background:linear-gradient(135deg,#e1d6c9,#9b8676)"></div><div class="copy"><a>Same Sex Relationships &amp; Counselling</a></div><div class="cta">Click Here ›</div></div>
  <div class="mini" style="top:1576px"><div class="pic" role="img" aria-label="Photo of a woman looking troubled" style="background:linear-gradient(135deg,#e6dcd2,#a38d7d)"></div><div class="copy">Are you living with a narcissist?</div><div class="cta">Click Here ›</div></div>
  <div class="mini" style="top:1709px"><div class="pic" role="img" aria-label="Photo of a distant couple in bed" style="background:linear-gradient(135deg,#dcd0c4,#8d7a6c)"></div><div class="copy">Is one of you an Intimacy Withholder?</div><div class="cta">Click Here ›</div></div>
  <div class="mini" style="top:1842px"><div class="pic" role="img" aria-label="Photo of a man at a laptop" style="background:linear-gradient(135deg,#c9d1d8,#6f7f8d)"></div><div class="copy">Is too much porn affecting your relationship?</div><div class="cta">Click Here ›</div></div>
  <div class="mini" style="top:1975px"><div class="pic" role="img" aria-label="Photo of an arguing couple" style="background:linear-gradient(135deg,#e0d3c7,#95776a)"></div><div class="copy">Is your relationship safe? Is your partner controlling?</div><div class="cta">Click Here ›</div></div>

  <div class="ad mood" style="top:2137px;height:163px" role="img" aria-label="Photo of a stressed woman"><div class="txt">Is Anxiety, Depression Or Stress bothering YOU?</div><div class="cta">Click Here ›</div></div>
  <div class="ad gp" style="top:2320px;height:157px" role="img" aria-label="Photo of a doctor at a desk"><div class="txt" style="top:36px">Information for referring GPs &amp; Health Professionals</div><div class="cta">Click Here ›</div></div>
</aside>

<section class="abs blog">
  <h2>Our Blog ( Relationships &amp; Sex )</h2>
  <div class="arrow" style="left:100px"><svg width="10" height="12" viewBox="0 0 10 12"><path d="M7 1L2 6l5 5" stroke="#fff" stroke-width="2" fill="none"/></svg></div>
  <div class="post" style="left:142px"><div class="pic" role="img" aria-label="Photo of a couple sitting apart" style="background:linear-gradient(135deg,#ddd5cc,#978a7f)"></div><span class="date">February 24, 2017</span><h5>What can I do if I'm living with a Narcissist?</h5><div class="more">Read More »</div></div>
  <div class="post" style="left:380px"><div class="pic" role="img" aria-label="Photo of a man looking away" style="background:linear-gradient(135deg,#d6d8da,#7f878d)"></div><span class="date">February 24, 2017</span><h5>Why am I with a Narcissist?</h5><div class="more">Read More »</div></div>
  <div class="post" style="left:618px"><div class="pic" role="img" aria-label="Photo of a couple in conversation" style="background:linear-gradient(135deg,#e4dacf,#a08a78)"></div><span class="date">February 24, 2017</span><h5>Why am I with a Narcissist?</h5><div class="more">Read More »</div></div>
  <div class="post" style="left:856px"><div class="pic" role="img" aria-label="Photo of a woman thinking" style="background:linear-gradient(135deg,#e1d8d2,#9c8a80)"></div><span class="date">February 24, 2017</span><h5>How Do I Know If I'm With a Narcissist?</h5><div class="more">Read More »</div></div>
  <div class="arrow" style="left:1072px"><svg width="10" height="12" viewBox="0 0 10 12"><path d="M3 1l5 5-5 5" stroke="#fff" stroke-width="2" fill="none"/></svg></div>
  <div class="readmore">Would you like to read more?<span class="btn">Click Here ›</span></div>
</section>

<footer class="abs footer">
  <div class="login">
    <h4>Members Login</h4>
    <div class="in">Enter Your Email...</div>
    <div class="in">Password</div>
    <div class="send">➤ Send</div>
  </div>
  <div class="foot-call">Call Us ☎ 1300 555 017</div>
  <div class="foot-links"><span>Privacy Policy</span>|<span>Terms &amp; Conditions</span>|<span>Site Map</span>|<span>Associate Psychologists Program</span>|<span>Contact Us</span></div>
  <div class="foot-social"><span></span><span></span><span></span></div>
  <div class="copy-note">© 2017 The Kelvale Clinic. All Rights Reserved · www.TheKelvaleClinic.com.au</div>
</footer>

</body>
</html>
```